Car rental website design for a UAE car rental company

This project is about creating a new website design for a car rental company located in Dubai (United Arab Emirates), I opened the same project a few months ago but I didn't receive a lot of appealing entries so I closed it but this time I am marking the project as guaranteed to avoid such situation again, if you have already provided a design before then please re-submit again on this project so that it is considered while reviewing all the designs

A few important things:

1- We need a simple non-complex design
2- The final deliverable would be 2 screens (PSD, JPEG ... etc), the first screen is for the home page and the second screen is for an internal page
3- The home page must have a section that end users can use to rent a car online directly from the home page instead of going into some inner pages
4- The current website is very old and not very appealing so avoid creating a similar design (www.crestvane-autos.example)
5- The name is Crestvane but the company rents normal cars (no Limousin cars will be rented) so avoid adding any fancy cars in the images/graphics used in the design, just normal end users cars
6- The expected pages would be: home, About us, Our team, Strategy, Contact us and links to social media pages
7- The attachments include the company's logo and some screens from other car rental companies that provide online rentals/payments

If you have any questions please feel free to ask and please note that we will need the designs urgently

Thanks

Target Market(s)

Dubai - United Arab Emirates

Industry/Entity Type

It Company

Number of Pages Required

2 page

Font styles to use
Sans Serif

Requirements
Must have
• Check the project details
Nice to have
Should not have

```html
<!DOCTYPE html>
<html lang="en">
<head>
<meta charset="utf-8">
<title>Crestvane Rent A Car</title>
<link href="https://fonts.googleapis.com/css2?family=Arimo:wght@400;700&family=Bitter:wght@400;500&family=Raleway:wght@700&family=Source+Sans+3:wght@400&display=swap" rel="stylesheet">
<style>
:root{
  --crimson:#a3002f;
  --red:#e00b12;
  --ink:#2b2b2b;
  --muted:#6d6d6d;
  --grey-logo:#7f8c86;
  --panel:#efefef;
  --nav-active:#c9c9c9;
  --white:#ffffff;
  --field:#f1f1f1;
  --footer:#8a9590;
}
*{margin:0;padding:0;box-sizing:border-box}
html,body{width:830px;height:1200px;overflow:hidden;background:var(--white)}
body{position:relative;font-family:"Arimo",Arial,sans-serif;color:var(--ink)}
h1,h2{font-weight:400}
.abs{position:absolute}

/* header */
.brand{left:80px;top:36px;display:flex;align-items:center;gap:10px}
.brand-mark{width:30px;height:30px;background:var(--crimson)}
.brand-name{font-family:"Bitter",serif;font-size:26px;font-weight:400;color:var(--grey-logo);line-height:1}
.brand-tag{left:120px;top:72px;font-family:"Bitter",serif;font-size:11px;letter-spacing:2px;color:var(--crimson)}
.header-photo{left:420px;top:10px;width:315px;height:124px;background:linear-gradient(90deg,#f3ead9 0%,#c8b8a0 30%,#8fa6c2 45%,#d4d7db 65%,#eef0f2 100%);border-radius:4px 4px 0 0}

/* nav */
.nav{left:0;top:134px;width:830px;height:28px;background:var(--crimson)}
.nav a{position:absolute;top:0;height:28px;line-height:28px;font-size:10px;color:var(--white);text-decoration:none;text-transform:uppercase}
.nav a.active{background:var(--nav-active);color:var(--ink);padding:0 10px}
.nav a.active::after{content:"";position:absolute;left:50%;bottom:-5px;margin-left:-5px;border:5px solid transparent;border-bottom:0;border-top-color:var(--nav-active)}

/* hero */
.hero{left:0;top:162px;width:830px;height:225px;background:radial-gradient(ellipse at 85% 60%,#5a1020 0%,transparent 55%),radial-gradient(ellipse at 10% 30%,#3a0d16 0%,transparent 50%),linear-gradient(180deg,#1b1b1e,#2a2225 60%,#1a1a1c)}
.hero-title{left:0;top:225px;width:830px;text-align:center;font-family:"Raleway",sans-serif;font-weight:700;font-size:27px;color:var(--white)}
.hero-sub{left:0;top:271px;width:830px;text-align:center;font-family:"Source Sans 3",sans-serif;font-size:15px;color:#e6e6e6}
.hero-btn{left:350px;top:322px;width:145px;height:30px;background:var(--crimson);border-radius:3px;color:var(--white);font-family:"Source Sans 3",sans-serif;font-size:13px;line-height:30px;text-align:center}

/* welcome */
.welcome{left:0;top:387px;width:830px;height:123px;background:var(--panel)}
.welcome-title{right:484px;top:424px;font-family:"Bitter",serif;font-size:21px;font-weight:400;letter-spacing:1px;color:var(--ink);text-align:right}
.welcome-sub{right:484px;top:457px;font-family:"Bitter",serif;font-size:16px;letter-spacing:1px;color:var(--crimson)}
.welcome-rule{left:369px;top:416px;height:74px;border-left:1px dotted #9a9a9a}
.welcome-text{left:388px;top:418px;width:365px;font-size:8.5px;line-height:11.5px;color:#444}
.welcome-text p+p{margin-top:12px}

/* services */
.section-title{left:0;top:544px;width:830px;text-align:center;font-family:"Bitter",serif;font-size:25px;font-weight:400;letter-spacing:1.5px;color:var(--ink)}
.card{top:623px;width:222px;height:207px;border:1px solid #ececec;border-top:0}
.card-photo{width:222px;height:132px}
.card-name{margin-top:10px;text-align:center;font-size:8.5px;font-weight:700;text-transform:uppercase}
.card-price{margin-top:4px;text-align:center;font-size:8.5px;color:var(--muted)}
.card-btn{display:block;margin:7px auto 0;width:72px;height:23px;line-height:23px;text-align:center;font-size:7px;font-weight:700;color:var(--white);background:var(--ink);text-transform:uppercase}
.card-btn.hot{background:var(--red)}

/* contact */
.contact{left:0;top:889px;width:830px;height:291px;background:radial-gradient(ellipse at 85% 55%,#5c0f1f 0%,transparent 55%),radial-gradient(ellipse at 30% 90%,#3a0c15 0%,transparent 45%),linear-gradient(180deg,#101012,#221c1e 60%,#151517)}
.contact-title{left:0;top:905px;width:830px;text-align:center;font-family:"Bitter",serif;font-size:26px;font-weight:500;color:var(--white)}
.field{left:82px;width:273px;background:var(--field);border-radius:2px;font-size:10px;color:#555;padding:8px 12px}
.submit{left:84px;top:1125px;width:69px;height:24px;background:var(--crimson);border-radius:3px;color:var(--white);font-size:11px;font-weight:700;line-height:24px;text-align:center}
.address-title{left:410px;top:972px;font-size:16px;color:var(--white);letter-spacing:1px}
.contact-line{left:410px;display:flex;align-items:center;gap:10px;font-size:12.5px;color:var(--white)}
.social{left:413px;top:1078px;display:flex;gap:10px}
.social span{width:15px;height:15px;background:#9a9a9a;border-radius:2px}

/* footer */
.footer{left:0;top:1180px;width:830px;height:20px;background:var(--footer);text-align:center;font-size:8px;line-height:22px;color:#222}
</style>
</head>
<body>

<header>
  <div class="abs brand"><span class="brand-mark"></span><span class="brand-name">Crestvane</span></div>
  <div class="abs brand-tag">Rent A Car</div>
  <div class="abs header-photo" role="img" aria-label="Family standing beside a silver family car"></div>
</header>

<nav class="abs nav">
  <a style="left:206px">Home</a>
  <a class="active" style="left:265px">About Us</a>
  <a style="left:364px">Our Team</a>
  <a style="left:454px">Strategy</a>
  <a style="left:542px">Contact Us</a>
</nav>

<section>
  <div class="abs hero" role="img" aria-label="Night highway with red light trails"></div>
  <h1 class="abs hero-title">EXPERIENCE AN EXTRA MILE</h1>
  <p class="abs hero-sub">of comfort, pleasure and leisure from the best</p>
  <div class="abs hero-btn">Make A booking</div>
</section>

<section>
  <div class="abs welcome"></div>
  <h2 class="abs welcome-title">WELCOME TO CRESTVANE</h2>
  <div class="abs welcome-sub">RENT A CAR</div>
  <div class="abs welcome-rule"></div>
  <div class="abs welcome-text">
    <p>As Dubai is expected to welcome millions of tourists and visitors, car rental industry is believed to escalate more rapidly in the region.</p>
    <p>Over the past five years, demands for car rentals in Dubai has been augmenting at a healthy pace and is currently registering a growth rate of 20 to 25 percent per year. The swift economic growth and the number.....</p>
  </div>
</section>

<section>
  <svg class="abs" style="left:80px;top:552px" width="670" height="20" aria-hidden="true">
    <g stroke="#b5b5b5" stroke-width="0.8">
      <line x1="0" y1="5" x2="230" y2="5"/><line x1="38" y1="9" x2="230" y2="9"/><line x1="68" y1="13" x2="230" y2="13"/>
      <line x1="430" y1="5" x2="660" y2="5"/><line x1="430" y1="9" x2="622" y2="9"/><line x1="430" y1="13" x2="590" y2="13"/>
    </g>
  </svg>
  <h2 class="abs section-title">OUR SERVICES</h2>

  <article class="abs card" style="left:65px">
    <div class="card-photo" role="img" aria-label="Grey sedan by a city waterfront" style="background:linear-gradient(180deg,#6d8595,#3e4c57 55%,#1d2328)"></div>
    <svg class="abs" style="left:94px;top:121px" width="34" height="6" aria-hidden="true"><g fill="none" stroke="#fff"><circle cx="3" cy="3" r="2.2"/><circle cx="23" cy="3" r="2.2"/><circle cx="31" cy="3" r="2.2"/></g><circle cx="13" cy="3" r="2.6" fill="#e00b12"/></svg>
    <div class="card-name">Arden Sedan 2.0 Diesel</div>
    <div class="card-price">Start from 39$/per a day</div>
    <span class="card-btn hot">Rent it</span>
  </article>

  <article class="abs card" style="left:304px">
    <div class="card-photo" role="img" aria-label="Red hatchback in front of a glass building" style="background:linear-gradient(180deg,#8fb2cf,#b8c4cc 50%,#7a8088)"></div>
    <div class="card-name">Lumo Hatch 2.0 Diesel</div>
    <div class="card-price">Start from 39$/per a day</div>
    <span class="card-btn">Rent it</span>
  </article>

  <article class="abs card" style="left:544px">
    <div class="card-photo" role="img" aria-label="Grey compact car on a city street at dusk" style="background:linear-gradient(180deg,#3a4a78,#5a5a66 50%,#2a2a30)"></div>
    <div class="card-name">Verra Compact 2.0 Diesel</div>
    <div class="card-price">Start from 39$/per a day</div>
    <span class="card-btn">Rent it</span>
  </article>
</section>

<section>
  <div class="abs contact" role="img" aria-label="Night highway with red light trails"></div>
  <svg class="abs" style="left:265px;top:919px" width="276" height="4" aria-hidden="true"><line x1="0" y1="2" x2="40" y2="2" stroke="#a3002f" stroke-width="2.5"/><line x1="236" y1="2" x2="276" y2="2" stroke="#a3002f" stroke-width="2.5"/></svg>
  <h2 class="abs contact-title">CONTACT US</h2>

  <div class="abs field" style="top:969px;height:27px">Full Name</div>
  <div class="abs field" style="top:1008px;height:27px">Email</div>
  <div class="abs field" style="top:1047px;height:66px">Message</div>
  <div class="abs submit">Submit</div>

  <div class="abs address-title">ADDRESS</div>
  <div class="abs contact-line" style="top:1012px">
    <svg width="19" height="19" viewBox="0 0 20 20" aria-hidden="true"><circle cx="10" cy="10" r="8.5" fill="none" stroke="#c4102f" stroke-width="1.5"/><path d="M7 5.5l2 2-1 1.5c.6 1.3 1.7 2.4 3 3l1.5-1 2 2-1.5 1.6C9.5 14.5 5.5 10.5 5.4 7z" fill="#c4102f"/></svg>
    <span>5550142876</span>
  </div>
  <div class="abs contact-line" style="top:1047px">
    <svg width="19" height="13" viewBox="0 0 19 13" aria-hidden="true"><rect x="0.7" y="0.7" width="17.6" height="11.6" fill="none" stroke="#c4102f" stroke-width="1.4"/><path d="M1 1l8.5 6.5L18 1" fill="none" stroke="#c4102f" stroke-width="1.4"/></svg>
    <span>info@crestvane-autos.example</span>
  </div>
  <div class="abs social"><span></span><span></span></div>
</section>

<footer class="abs footer">© 2015 Crestvane. All Rights Reserved.</footer>

</body>
</html>
```